Professional Services - letterhead / business cards

The company (velmora partners) will provide services to Investment Funds and large investors in Spain. I have recently chosen a logo that I am attaching.

I would like a simple stationary design that i could use as letter head, business cards and "with compliments" cards.

I am not quite sure which color I will mostly use for the logo, in the email signature I will probably lean towards the white background and grey letters. I am attaching my favourite options.

Target Market(s)

Large Multinationals, Investment funds and Law firms

Industry/Entity Type

Business

Requirements
Must have
• my details are:
Luis R. Abadal
Velmora Partners S.L.
Casa de Torrelumbre
Calle de Vientoalto 27
28014 Madrid
T: +34 (91) 387-2265
M: +34 (646) 819-054
e-mail: labadal@velmorapartners.com

```html
<!DOCTYPE html>
<html lang="en">
<head>
<meta charset="utf-8">
<title>Velmora Partners – Business Cards</title>
<link rel="stylesheet" href="https://fonts.googleapis.com/css2?family=Questrial&display=swap">
<style>
  :root {
    --page-bg: #8e8e8e;
    --card-back: #3c3c3c;
    --card-front: #5b5b5b;
    --frame-light: #d9d9d9;
    --text-light: #e4e4e4;
    --emboss-line: #4a4a4a;
    --emboss-text: #474747;
  }
  * { margin: 0; padding: 0; box-sizing: border-box; }
  html, body {
    width: 1200px;
    height: 900px;
    overflow: hidden;
    background: var(--page-bg);
    font-family: "Questrial", "Century Gothic", sans-serif;
  }
  .canvas {
    position: relative;
    width: 1200px;
    height: 900px;
  }
  .card {
    position: absolute;
    width: 520px;
    height: 336px;
  }
  .card--details {
    left: 55px;
    top: 282px;
    background: var(--card-back);
    color: var(--text-light);
  }
  .card--brand {
    left: 625px;
    top: 282px;
    background: var(--card-front);
  }
  .card__frame {
    position: absolute;
    inset: 14px;
    border: 1px solid var(--frame-light);
  }
  .card--brand .card__frame {
    inset: 18px;
    border: 1.5px solid var(--emboss-line);
  }
  .details {
    position: absolute;
    left: 40px;
    top: 36px;
    right: 40px;
  }
  .details__name {
    font-size: 21px;
    letter-spacing: 0.08em;
    text-transform: uppercase;
    font-weight: 400;
  }
  .details__company {
    font-size: 13px;
    margin-top: 2px;
    letter-spacing: 0.02em;
  }
  .details__contacts {
    list-style: none;
    margin-top: 26px;
    font-size: 13px;
    line-height: 1.45;
  }
  .details__contacts li { display: flex; }
  .details__label { width: 22px; }
  .details__address {
    font-style: normal;
    margin-top: 24px;
    font-size: 13px;
    line-height: 1.45;
  }
  .brand-name {
    position: absolute;
    left: 0;
    right: 0;
    top: 50%;
    transform: translateY(-50%);
    text-align: center;
    font-size: 44px;
    color: var(--emboss-text);
    letter-spacing: 0.01em;
  }
</style>
</head>
<body>
<main class="canvas">
  <section class="card card--details" aria-label="Business card, details side">
    <div class="card__frame"></div>
    <div class="details">
      <h1 class="details__name">Luis R. Abadal</h1>
      <p class="details__company">Velmora Partners S.L.</p>
      <ul class="details__contacts">
        <li><span class="details__label">T</span>+34 (91) 387-2265</li>
        <li><span class="details__label">M</span>+34 (646) 819-054</li>
        <li><span class="details__label">E</span>labadal@velmorapartners.com</li>
      </ul>
      <address class="details__address">
        Casa de Torrelumbre<br>
        Calle de Vientoalto 27, 28014 Madrid
      </address>
    </div>
  </section>

  <section class="card card--brand" aria-label="Business card, brand side">
    <div class="card__frame"></div>
    <p class="brand-name">velmora partners</p>
  </section>
</main>
</body>
</html>
```